Business Card & Letterhead Design

We a financial advice company based in Australia. We provide advice to wealthy farmers.

We are changing our business name FROM Brightvale Financial TO Tallowmere Wealth and we need a new letterhead and double sided business card design

Attached is designs from our previous branding (Brightvale Financial) as it includes all the details we require on the new Tallowmere Wealth business cards and letterhead.

Need extra days to review

```html
<!DOCTYPE html>
<html lang="en">
<head>
<meta charset="utf-8">
<title>Tallowmere Wealth – Business Cards</title>
<link rel="stylesheet" href="https://fonts.googleapis.com/css2?family=Montserrat:wght@400;500;700&display=swap">
<style>
  :root {
    --backdrop: #3a2e28;
    --card: #2f3032;
    --card-edge: #1c1d1f;
    --silver: #d9d9db;
    --silver-mid: #b4b5b8;
    --silver-dim: #8e8f93;
    --white: #f4f4f4;
  }
  * { box-sizing: border-box; margin: 0; padding: 0; }
  html, body { width: 1200px; height: 800px; overflow: hidden; }
  body {
    background: var(--backdrop);
    font-family: "Montserrat", Arial, sans-serif;
    position: relative;
  }
  .card {
    position: absolute;
    background: var(--card);
    border-radius: 4px;
    box-shadow: 0 0 0 1px var(--card-edge), 0 14px 30px rgba(0,0,0,.45);
    overflow: hidden;
  }

  /* Front card */
  .card-front {
    left: 70px; top: 110px; width: 500px; height: 290px;
    text-align: center;
    color: var(--silver-mid);
  }
  .brand-mark {
    width: 58px; height: 58px; margin: 26px auto 10px;
    border: 2px solid var(--silver); border-radius: 50%;
  }
  .brand-name {
    font-size: 25px; font-weight: 500; letter-spacing: 3px;
    color: var(--silver); text-transform: uppercase; line-height: 1.1;
  }
  .brand-tagline {
    font-size: 10.5px; letter-spacing: 4.2px; text-transform: uppercase;
    color: var(--silver-mid); margin-top: 3px;
  }
  .services { margin-top: 16px; font-size: 12.5px; line-height: 1.45; color: var(--silver); }
  .licensee { margin-top: 16px; font-size: 11.5px; line-height: 1.45; color: var(--silver-dim); }

  /* Back card */
  .card-back {
    left: 610px; top: 340px; width: 540px; height: 310px;
    color: var(--white);
  }
  .back-emblem {
    position: absolute; left: -80px; top: 10px; width: 290px; height: 290px;
    border: 9px solid var(--silver); border-radius: 50%;
    display: flex; align-items: center; justify-content: center;
  }
  .back-emblem span {
    font-size: 20px; font-weight: 500; letter-spacing: 2px; color: var(--silver);
    text-transform: uppercase; margin-left: 60px; text-align: center; line-height: 1.3;
  }
  .back-details { position: absolute; left: 255px; top: 26px; right: 18px; }
  .motto { text-align: right; font-size: 13px; font-weight: 700; letter-spacing: .4px; }
  .person { margin-top: 12px; }
  .person-name { font-size: 15px; font-weight: 700; }
  .person-name small { font-size: 11px; font-weight: 400; }
  .person-role { font-size: 12px; line-height: 1.35; color: var(--silver); }
  .contacts { list-style: none; margin-top: 8px; font-size: 12.5px; line-height: 1.4; letter-spacing: .5px; }
  .contacts li { display: flex; align-items: center; gap: 6px; }
  .contacts svg { width: 11px; height: 11px; fill: var(--silver); flex: none; }
  .address { margin-top: 12px; font-size: 12px; line-height: 1.4; color: var(--silver-mid); }
  .referral { margin-top: 12px; font-size: 13px; letter-spacing: .8px; color: var(--silver-dim); }
</style>
</head>
<body>

<section class="card card-front" aria-label="Business card front">
  <div class="brand-mark" aria-hidden="true"></div>
  <div class="brand-name">Tallowmere Wealth</div>
  <div class="brand-tagline">Strategic Financial Advice</div>
  <div class="services">
    Personal &amp; Business Insurance Solutions<br>
    Business Estate Planning<br>
    Succession Planning
  </div>
  <div class="licensee">
    Meridian Advice Partners Limited<br>
    Australian Financial Services Licensee License Number 500812
  </div>
</section>

<section class="card card-back" aria-label="Business card back">
  <div class="back-emblem"><span>Tallowmere<br>Wealth</span></div>
  <div class="back-details">
    <p class="motto">‘Financial peace of mind’</p>
    <div class="person">
      <div class="person-name">Sam Hartley <small>B.Ag.Ec. Dip F.P. CFP®</small></div>
      <div class="person-role">Managing Director<br>Authorised Representative</div>
    </div>
    <ul class="contacts">
      <li><svg viewBox="0 0 12 12"><path d="M2.5 1l2 2.2-1 1.3c.7 1.5 1.8 2.6 3.3 3.3l1.3-1 2.2 2-.9 1.6C5.6 10.2 1.8 6.4 1 2z"/></svg>(07) 3100 2458</li>
      <li><svg viewBox="0 0 12 12"><rect x="1" y="4" width="10" height="6" rx="1"/><rect x="3" y="1" width="6" height="3"/></svg>(07) 3100 2459</li>
      <li><svg viewBox="0 0 12 12"><rect x="3" y="0.5" width="6" height="11" rx="1"/></svg>0400 118 362</li>
      <li><svg viewBox="0 0 12 12"><path d="M1 2.5h10v7H1z M1 2.5l5 4 5-4" stroke="#2f3032" stroke-width=".8"/></svg>sam@brightvalefinancial.com.au</li>
      <li><svg viewBox="0 0 12 12"><circle cx="6" cy="6" r="5.5"/><path d="M.5 6h11M6 .5v11" stroke="#2f3032" stroke-width=".8"/></svg>www.brightvalefinancial.com.au</li>
    </ul>
    <p class="address">
      Suite 4A, 18 Corwin St<br>
      Harbourside QLD 4170<br>
      PO Box 5120, Eastbank QLD 4170
    </p>
    <p class="referral">A referral built business</p>
  </div>
</section>

</body>
</html>
```